Wandering Rooms Stationary Set

Wandering Rooms is a bespoke interior design firm set to provide services to VIP clients with elegance and minimalism is the main theme for our stationary set. We require a full stationary set covering A4 letterhead, A4 & A3 envelopes, business cards, USB's, CDs, email signature and any other item the designer sees fit. logo is already designed and finalized, and we require the designer to use it as is without modifying the logo.

Address to be used on letterhead / business cards ...etc shall be as follows:

Phone : +971 2 518 2047
P.O. Box : 309186
Address: Block C&D, Bldg. 47, Court 12, Abu Dhabi, United Arab Emirates
Website: www.wanderingrooms-example.com

Target Market(s)

VIP Clients

Industry/Entity Type

Interior Design

Font styles to use
Other font styles liked:
• something to be unique

Colors

Designer to choose colors to be used in the design.

Requirements
Must have
• Elegant, minimalistic
Nice to have
• Simple yet elegant design having a sharp yet clean cut format
Should not have
• No additional colours, just colours that are used in the logo (silver, black or gold)

```html
<!DOCTYPE html>
<html lang="en">
<head>
<meta charset="utf-8">
<title>Wandering Rooms – Business Cards</title>
<link rel="stylesheet" href="https://fonts.googleapis.com/css2?family=Cormorant+Garamond:wght@400;500&family=Great+Vibes&display=swap">
<style>
  :root {
    --backdrop: #e4e4e6;
    --card-black: #070707;
    --gold: #c9a24e;
    --gold-edge: #b8913f;
    --silver: #cfcfd2;
    --white: #f2f2f2;
    --divider: #3a3a3a;
  }
  * { box-sizing: border-box; margin: 0; padding: 0; }
  html, body {
    width: 1200px; height: 800px; overflow: hidden;
    background: var(--backdrop);
  }
  .stage {
    position: relative; width: 1200px; height: 800px;
    display: flex; align-items: center; justify-content: center; gap: 40px;
  }
  .card {
    position: relative;
    width: 520px; height: 297px;
    background: var(--card-black);
    border: 2px solid var(--gold-edge);
    box-shadow: 0 14px 30px rgba(0,0,0,0.25);
    font-family: "Cormorant Garamond", serif;
  }
  /* Info side */
  .card-info .brand {
    position: absolute; left: 34px; top: 0; bottom: 0; width: 240px;
    display: flex; align-items: center; justify-content: center;
  }
  .brand-name {
    font-family: "Cormorant Garamond", serif;
    font-weight: 500; font-size: 34px; letter-spacing: 1px;
    color: var(--gold); white-space: nowrap;
  }
  .divider {
    position: absolute; left: 288px; top: 78px; height: 142px;
    width: 1px; background: var(--divider);
  }
  .details {
    position: absolute; left: 306px; top: 66px; right: 14px;
    color: var(--white);
  }
  .person-name {
    font-family: "Great Vibes", cursive;
    font-size: 26px; color: var(--gold); line-height: 1;
  }
  .person-title { font-size: 15px; margin-bottom: 10px; }
  .address { font-size: 11.5px; line-height: 1.3; margin-bottom: 10px; }
  .contact-list { list-style: none; font-size: 11.5px; line-height: 1.45; }
  .contact-list li { display: flex; align-items: center; gap: 6px; white-space: nowrap; }
  .contact-list svg { width: 9px; height: 9px; flex: none; }
  /* Logo side */
  .card-logo { display: flex; align-items: center; justify-content: center; }
  .card-logo .brand-name { color: var(--silver); font-size: 46px; }
</style>
</head>
<body>
<main class="stage">
  <section class="card card-info">
    <div class="brand"><span class="brand-name">Wandering Rooms</span></div>
    <div class="divider"></div>
    <div class="details">
      <p class="person-name">Daniel Hart</p>
      <p class="person-title">President</p>
      <p class="address">P.O. Box : 309186,<br>Block C&amp;D, Bldg. 47, Court 12<br>Abu Dhabi, United Arab Emirates</p>
      <ul class="contact-list">
        <li>
          <svg viewBox="0 0 10 10" aria-hidden="true"><path fill="#c9a24e" d="M2 0.5 L3.6 0.5 L4.2 3 L3 3.8 Q4 6 6.2 7 L7 5.8 L9.5 6.4 L9.5 8 Q9.5 9.5 8 9.5 Q0.5 9 0.5 2 Q0.5 0.5 2 0.5Z"/></svg>
          +971 2 518 2047
        </li>
        <li>
          <svg viewBox="0 0 10 10" aria-hidden="true"><rect x="0.5" y="2" width="9" height="6.5" fill="#c9a24e"/><path d="M0.8 2.3 L5 5.6 L9.2 2.3" fill="none" stroke="#070707" stroke-width="0.9"/></svg>
          info@wanderingrooms-example.com
        </li>
        <li>
          <svg viewBox="0 0 10 10" aria-hidden="true"><circle cx="5" cy="5" r="4.3" fill="none" stroke="#c9a24e" stroke-width="1.1"/><ellipse cx="5" cy="5" rx="1.8" ry="4.3" fill="none" stroke="#c9a24e" stroke-width="0.9"/><line x1="0.7" y1="5" x2="9.3" y2="5" stroke="#c9a24e" stroke-width="0.9"/></svg>
          www.wanderingrooms-example.com
        </li>
      </ul>
    </div>
  </section>
  <section class="card card-logo">
    <span class="brand-name">Wandering Rooms</span>
  </section>
</main>
</body>
</html>
```